Medical group practice

We need a flyer design incorporating the three doctors in the practice, there is a general practitioner, ophthalmologist and an obstetrician & Gynaecologist. see the attached file for the concept. will leave the colour design up to you

Target Market(s)

general public

Industry/Entity Type

Health Care

Colors

Designer to choose colors to be used in the design.

Requirements
Must have
• logos included in attachement

```html
<!DOCTYPE html>
<html lang="en">
<head>
<meta charset="utf-8">
<title>Crestview Medical Flyer</title>
<link href="https://fonts.googleapis.com/css2?family=Ubuntu:wght@400;500;700&family=Oswald:wght@500;600&family=Roboto:wght@400&display=swap" rel="stylesheet">
<style>
:root{
  --backdrop:#000;
  --paper:#fff;
  --cream:#f6efde;
  --brand-red:#c4222b;
  --brand-grey:#6d6e71;
  --ink:#222;
  --blue:#0a6fa8;
  --purple:#82127f;
  --navy:#0b3a6b;
  --yellow:#f7e600;
  --green:#009a3a;
  --bar-grey:#58595b;
}
*{margin:0;padding:0;box-sizing:border-box}
html,body{width:1165px;height:1200px;overflow:hidden;background:var(--backdrop)}
.canvas{position:relative;width:1165px;height:1200px;background:var(--backdrop)}
.size-note{position:absolute;left:252px;top:70px;color:#fff;font:400 15px "Roboto",sans-serif}
.flyer{position:absolute;left:253px;top:93px;width:659px;height:1018px;background:var(--paper);overflow:hidden}
.header{position:absolute;left:0;top:0;width:659px;height:269px;background:linear-gradient(90deg,#f3f5f7 0%,#eef2f5 55%,#e4ecef 100%)}
.header-photo{position:absolute;right:0;top:0;width:240px;height:269px;
  background:radial-gradient(ellipse at 60% 55%,#cfd9dd 0%,#b9cfd6 40%,#dfe7ea 75%,rgba(238,242,245,0) 100%)}
.brand{position:absolute;left:89px;top:104px;font:700 32px "Ubuntu",sans-serif;letter-spacing:.2px;white-space:nowrap}
.brand .red{color:var(--brand-red)}
.brand .grey{color:var(--brand-grey)}
.brand-dot{position:absolute;left:38px;top:106px;width:34px;height:34px;border-radius:50%;background:var(--brand-red)}
.tagline{position:absolute;left:89px;top:145px;font:400 23px "Ubuntu",sans-serif;color:#3d3d3f;white-space:nowrap;letter-spacing:.3px}
.address{position:absolute;left:40px;top:177px;width:421px;height:20px;background:var(--bar-grey);color:#fff;
  font:500 14px "Oswald",sans-serif;text-align:center;line-height:20px;white-space:nowrap}
.bands{position:absolute;left:0;top:269px;width:659px;height:108px;display:flex;gap:2px;background:#fff}
.band{flex:1;display:flex;flex-direction:column;align-items:center;justify-content:center;text-align:center}
.band.gp{background:var(--blue)}
.band.eye{background:var(--purple)}
.band.obgyn{background:var(--navy)}
.band h2{color:var(--yellow);font:700 20px/19px "Ubuntu",sans-serif;margin-bottom:5px}
.band p{color:#fff;font:700 15px/19px "Ubuntu",sans-serif;display:flex;align-items:flex-start;gap:3px}
.band p svg{margin-top:3px;flex:none}
.doctor{position:absolute;left:0;width:659px;height:192px;background:linear-gradient(180deg,var(--cream) 0%,#fbf8f1 45%,#fff 100%)}
.doctor.one{top:377px}
.doctor.two{top:569px}
.doctor.three{top:761px}
.doctor-mark{position:absolute;left:80px;top:54px;width:84px;height:84px;border-radius:50%}
.one .doctor-mark{background:var(--blue)}
.two .doctor-mark{background:var(--purple)}
.three .doctor-mark{background:var(--navy)}
.info{position:absolute;left:207px}
.one .info{top:42px}
.two .info{top:30px}
.three .info{top:34px}
.practice{font:600 30px/36px "Oswald",sans-serif;color:var(--ink);letter-spacing:.2px}
.name{font:700 32px/38px "Ubuntu",sans-serif;white-space:nowrap}
.one .name{color:var(--blue);margin-left:-5px}
.two .name{color:var(--purple)}
.three .name{color:var(--navy)}
.cred{font:500 22px/27px "Ubuntu",sans-serif;color:#2a2a2a;white-space:nowrap}
.mail{display:flex;align-items:center;gap:9px;font:500 22px/27px "Ubuntu",sans-serif;color:#1e1e1e;white-space:nowrap}
.hours{position:absolute;left:0;top:953px;width:659px;height:65px;background:var(--green);text-align:center;padding-top:9px}
.hours h3{color:var(--yellow);font:700 20px/22px "Ubuntu",sans-serif;letter-spacing:-.3px}
.hours p{color:#fff;font:700 20px/24px "Ubuntu",sans-serif;letter-spacing:-.4px}
</style>
</head>
<body>
<div class="canvas">
  <div class="size-note">Size 5.5x8.5 inches</div>
  <div class="flyer">
    <header class="header">
      <div class="header-photo" role="img" aria-label="Photo of a medical professional in surgical cap and mask"></div>
      <div class="brand-dot"></div>
      <div class="brand"><span class="red">CRESTVIEW</span> <span class="grey">MEDICAL</span></div>
      <div class="tagline">YOUR HEALTH IS OUR PRIORITY</div>
      <div class="address">42 Harbour Road, Port Sable, St. Alden. Tel : (555) 210 4400 / 4401</div>
    </header>

    <section class="bands">
      <div class="band gp">
        <h2>General<br>Practitioner</h2>
        <p><svg width="14" height="14" viewBox="0 0 14 14"><circle cx="7" cy="7" r="6" fill="none" stroke="#fff" stroke-width="1.4"/><path d="M5 3.5c-1 1-1 5 1.5 6.5l1-1.2-1.2-1.3L7 6 5.8 4.2z" fill="#fff"/></svg>(555) 310 2277</p>
      </div>
      <div class="band eye">
        <h2>Ophthalmologist</h2>
        <p><svg width="14" height="14" viewBox="0 0 14 14"><circle cx="7" cy="7" r="6" fill="none" stroke="#fff" stroke-width="1.4"/><path d="M5 3.5c-1 1-1 5 1.5 6.5l1-1.2-1.2-1.3L7 6 5.8 4.2z" fill="#fff"/></svg>(555) 320 5186</p>
      </div>
      <div class="band obgyn">
        <h2>Obstetrician/<br>Gynaecologist</h2>
        <p><svg width="14" height="14" viewBox="0 0 14 14"><circle cx="7" cy="7" r="6" fill="none" stroke="#fff" stroke-width="1.4"/><path d="M5 3.5c-1 1-1 5 1.5 6.5l1-1.2-1.2-1.3L7 6 5.8 4.2z" fill="#fff"/></svg><span>(555) 330 7042,<br>(555) 340 9915</span></p>
      </div>
    </section>

    <section class="doctor one">
      <div class="doctor-mark"></div>
      <div class="info">
        <div class="name">Dr. Nolan Whitcombe</div>
        <div class="cred">MD, General Practitioner</div>
        <div class="mail"><svg width="25" height="16" viewBox="0 0 25 16"><rect width="25" height="16" fill="var(--blue)"/><path d="M0 0l12.5 9L25 0M0 16l9-8M25 16l-9-8" stroke="#fff" stroke-width="1.6" fill="none"/></svg>nolan.whitcombe.md@mailbox.com</div>
      </div>
    </section>

    <section class="doctor two">
      <div class="doctor-mark"></div>
      <div class="info">
        <div class="practice">Clearview Eye Care Services</div>
        <div class="name">Dr. Lucienne R. Ferrante</div>
        <div class="cred">MD, Surgeon Ophthalmologist</div>
        <div class="mail"><svg width="25" height="16" viewBox="0 0 25 16"><rect width="25" height="16" fill="var(--purple)"/><path d="M0 0l12.5 9L25 0M0 16l9-8M25 16l-9-8" stroke="#fff" stroke-width="1.6" fill="none"/></svg>lucienne.eyes@mailbox.com</div>
      </div>
    </section>

    <section class="doctor three">
      <div class="doctor-mark"></div>
      <div class="info">
        <div class="name">Dr. Marcus Delacroix</div>
        <div class="cred">BMedSci, MBBS, DM (O&amp;G), FACOG</div>
        <div class="cred">Obstetrician &amp; Gynaecologist</div>
        <div class="mail"><svg width="25" height="16" viewBox="0 0 25 16"><rect width="25" height="16" fill="var(--navy)"/><path d="M0 0l12.5 9L25 0M0 16l9-8M25 16l-9-8" stroke="#fff" stroke-width="1.6" fill="none"/></svg>drdelacroix@mailbox.com</div>
      </div>
    </section>

    <footer class="hours">
      <h3>OPENING HOURS :</h3>
      <p>Monday - Fridays : 9am - 6pm &bull;&nbsp; Saturdays : 10am - 5pm</p>
    </footer>
  </div>
</div>
</body>
</html>
```